2023 Cheers to 50 Years Graphic

Hi - I'd like a high-res image that's also print ready that we can use around our office with our 2023 slogan: Cheers to 50 years!

Ideally we'd like a catchy image, the slogan and our logo.

I'll attach the 2022 example. Please use our 50th anniversary logo also attached.

Graphic could be anything celebratory!

Main demographic is males.

Maybe cheers of champagne glasses or beer. But open top option that does not involve alcohol too.

```html
<!DOCTYPE html>
<html lang="en">
<head>
<meta charset="utf-8">
<title>Cheers to 50 Years – 2023</title>
<link rel="stylesheet" href="https://fonts.googleapis.com/css2?family=Lobster+Two:ital,wght@0,700;1,700&display=swap">
<style>
  :root {
    --ink-navy: #2d3a80;
    --spark-core: #fffbe8;
    --spark-gold: #f6c94a;
    --spark-amber: #c98a1e;
    --night-dark: #2a1d0c;
    --teal-haze: #7fb2b6;
  }
  html, body {
    margin: 0;
    padding: 0;
    width: 1200px;
    height: 814px;
    overflow: hidden;
    background: #ffffff;
  }
  .poster {
    position: relative;
    width: 1200px;
    height: 814px;
    overflow: hidden;
    font-family: "Lobster Two", cursive;
    color: var(--ink-navy);
  }
  .sparkler-photo {
    position: absolute;
    inset: 0;
    background:
      radial-gradient(ellipse 260px 220px at 640px 330px, var(--spark-core) 0%, rgba(255,244,200,0.85) 40%, rgba(255,230,150,0) 100%),
      radial-gradient(ellipse 200px 200px at 330px 520px, rgba(255,250,225,0.95) 0%, rgba(255,238,170,0.6) 45%, rgba(255,230,150,0) 100%),
      radial-gradient(ellipse 560px 460px at 620px 380px, var(--spark-gold) 0%, rgba(226,170,60,0.7) 50%, rgba(150,100,30,0) 100%),
      radial-gradient(ellipse 520px 380px at 1100px 760px, var(--teal-haze) 0%, rgba(127,178,182,0) 100%),
      radial-gradient(ellipse 420px 300px at 200px 780px, rgba(170,200,200,0.7) 0%, rgba(170,200,200,0) 100%),
      linear-gradient(160deg, var(--night-dark) 0%, var(--spark-amber) 45%, #b99a5c 75%, #8fb4b4 100%);
  }
  .headline {
    position: absolute;
    left: 0;
    right: 0;
    margin: 0;
    text-align: center;
    font-weight: 700;
    line-height: 1;
    white-space: nowrap;
  }
  .headline-year {
    top: 150px;
    left: 420px;
    right: auto;
    width: 300px;
    font-style: normal;
    font-size: 142px;
  }
  .headline-slogan {
    top: 300px;
    left: 100px;
    right: auto;
    width: 980px;
    font-style: italic;
    font-size: 136px;
    letter-spacing: -1px;
  }
  .company-name {
    position: absolute;
    left: 860px;
    top: 632px;
    width: 260px;
    text-align: center;
    font-weight: 700;
    font-style: normal;
    font-size: 30px;
    line-height: 1;
    white-space: nowrap;
  }
</style>
</head>
<body>
  <main class="poster">
    <div class="sparkler-photo" role="img" aria-label="Close-up photograph of burning golden sparklers throwing bright sparks against a dark warm background"></div>
    <h1 class="headline headline-year">2023</h1>
    <p class="headline headline-slogan">Cheers to 50 years!</p>
    <p class="company-name">Harborline Supply</p>
  </main>
</body>
</html>
```